EB-5 Regional Center needs a Web design

Harlow Ridge Financial Partners is an expanding EB-r regional center. We have been successful in sponsoring multiple projects of third-party developers and placing EB-5, B-1, and Private Investments into multiple projects.

We are now partnering directly with project developers in the energy and healthcare to raise foreign capital for projects in those industries. The foreign capital is used as project equity and our collective balance sheets are used to guarantee debt to complete the funding of the projects.

We need a web site where we can post our company credentials, the bios of each partner, a document page for each of our projects where we can post specific project related documents which foreign investors can read, and we will need a section where foreign investors can fill out investor forms confirming that they are qualified investors and leaving their contact so that our agents and executives can make contact.

The final design should reflect the exceptional experience of the partners and our financial strength and stability.

We do have a logo we would want to use on the web design.

Target Market(s)

EB-5 Investors, B-1 Investors, Private Equity and other investors seeking quality investment in job creating US projects.

Coding

Number of Pages Required

5+ page

Font styles to use
Sans Serif

Requirements
Must have
• Pages to display company info, partner bios, projects completed, and a projects in-process page where we can post documents and info on projects for which we are seeking foreign investment. We also need a section where investors can enter their qualifying personal information and leave contact information for us.

```html
<!DOCTYPE html>
<html lang="en">
<head>
<meta charset="utf-8">
<title>Harlow Ridge Financial Partners</title>
<link href="https://fonts.googleapis.com/css2?family=Montserrat:wght@500;600;700;800&family=Roboto:wght@400;500&display=swap" rel="stylesheet">
<style>
:root{
  --black:#000;
  --ink:#1a1a1a;
  --white:#fff;
  --grey-bg:#e6e6e6;
  --grey-text:#666;
  --light-text:#c9c9c9;
  --navy-1:#0d2333;
  --navy-2:#1f4a66;
  --slate:#4a4a4a;
  --line:#d4d4d4;
  --head:'Montserrat',Arial,sans-serif;
  --body:'Roboto',Arial,sans-serif;
}
*{margin:0;padding:0;box-sizing:border-box}
html,body{width:1200px;height:4702px;overflow:hidden}
body{position:relative;background:var(--white);font-family:var(--body);color:var(--ink)}
.abs{position:absolute}
.btn{display:inline-block;font-family:var(--head);font-weight:700;font-size:14px;letter-spacing:.5px;border-radius:24px;text-align:center}
.btn-dark{background:var(--black);color:var(--white);padding:15px 26px}
.section-title{font-family:var(--head);font-weight:700;font-size:27px;letter-spacing:.5px;text-align:center}
.section-lead{font-size:13.5px;line-height:24px;text-align:center;color:var(--slate)}

/* header */
.site-header{left:0;top:0;width:1200px;height:95px;background:var(--black)}
.brand{left:173px;top:26px;color:var(--white);font-family:var(--head);font-weight:600;font-size:17px;line-height:21px;letter-spacing:.5px;display:flex;align-items:center;gap:10px}
.brand-mark{width:22px;height:22px;border-radius:50%;background:var(--white);flex:none}
.nav{top:33px;left:0;width:1200px;height:34px}
.nav a{position:absolute;top:0;height:34px;line-height:34px;color:var(--white);font-family:var(--head);font-weight:700;font-size:12.5px;text-decoration:none}
.nav a.active{border:2px solid var(--white);border-radius:4px;padding:0 10px;line-height:30px}

/* hero */
.hero{left:0;top:95px;width:1200px;height:648px;background:linear-gradient(120deg,#0a1a26 0%,var(--navy-1) 30%,var(--navy-2) 60%,#0f2a3d 100%);clip-path:polygon(0 0,100% 0,100% 632px,0 643px)}
.hero-title{left:0;top:175px;width:1200px;text-align:center;color:var(--white);font-family:var(--head);font-weight:700;font-size:52px;line-height:64px;letter-spacing:1px}
.hero-btn{left:509px;top:332px;width:182px;height:50px;line-height:46px;border:2px solid var(--white);border-radius:25px;background:var(--black);color:var(--white);font-family:var(--head);font-weight:700;font-size:16px;text-align:center}
.hero-arrow{top:273px}

/* about */
.about{left:0;top:738px;width:1200px;height:590px;background:var(--grey-bg)}
.about-title{left:628px;top:92px;font-family:var(--head);font-weight:700;font-size:29px;line-height:33px}
.about-text{left:628px;top:176px;width:402px;font-size:13.5px;line-height:24px;color:var(--grey-text);text-align:justify}
.about .btn{left:626px;top:392px}

/* projects */
.projects{left:0;top:1328px;width:1200px;height:836px}
.projects .section-title{position:absolute;top:72px;left:0;width:1200px}
.projects .section-lead{position:absolute;top:118px;left:0;width:1200px}
.card{width:266px;height:263px;background:var(--white);box-shadow:0 2px 8px rgba(0,0,0,.18)}
.card-img{height:178px}
.card-title{padding:18px 27px 0;font-family:var(--head);font-weight:700;font-size:16.5px;line-height:23px;color:#2a2a2a}

/* band */
.band-strip{left:0;top:2164px;width:1200px;height:30px;background:#8e8e8e;clip-path:polygon(0 0,100% 0,100% 4px,0 20px)}
.band{left:0;top:2164px;width:1200px;height:403px;background:linear-gradient(90deg,#1b1b1b,#2a2826 50%,#1a1a1a);clip-path:polygon(0 8px,100% 0,100% 370px,0 403px)}
.band-title{left:0;top:122px;width:1200px;text-align:center;color:var(--white);font-family:var(--head);font-weight:700;font-size:20.5px;line-height:35px;letter-spacing:.5px}
.band-btn{left:512px;top:224px;width:176px;height:46px;line-height:42px;border:2px solid var(--white);border-radius:23px;color:var(--white);font-family:var(--head);font-weight:700;font-size:12.5px;text-align:center;background:var(--black)}

/* in process */
.inprocess{left:0;top:2567px;width:1200px;height:532px}
.inprocess-title{left:170px;top:92px;font-family:var(--head);font-weight:700;font-size:27.5px}
.inprocess-text{left:172px;top:146px;width:384px;font-size:13.5px;line-height:24px;color:var(--slate);text-align:justify}
.inprocess .btn{left:172px;top:381px}
.inprocess-img{left:661px;top:48px;width:398px;height:392px;border-radius:10px;background:linear-gradient(135deg,#0b1f2c 0%,#2e5571 45%,#a89c94 75%,#d9d3cd 100%)}

/* partners */
.partners{left:0;top:3099px;width:1200px;height:644px;background:var(--black);color:var(--white)}
.partners .section-title{position:absolute;top:70px;left:0;width:1200px;color:var(--white)}
.partners .section-lead{position:absolute;top:116px;left:0;width:1200px;color:var(--white)}
.bio{top:217px;width:300px;text-align:center}
.bio-photo{width:170px;height:170px;border-radius:50%;margin:0 auto;background:radial-gradient(circle at 50% 40%,#c9b6a4 0%,#7c8fa6 55%,#dfe3e8 100%)}
.bio-name{margin-top:28px;font-family:var(--head);font-weight:700;font-size:14.5px;letter-spacing:.5px}
.bio-rule{width:40px;height:1px;background:#9a9a9a;margin:12px auto 12px}
.bio-text{font-size:13.5px;line-height:24px;color:var(--light-text)}
.bio-link{width:26px;height:26px;border:1.5px solid var(--white);border-radius:50%;margin:16px auto 0}
.bio-divider{top:230px;width:1px;height:270px;background:#2e2e2e}

/* quote */
.quote{left:0;top:3743px;width:1200px;height:555px;background:linear-gradient(90deg,#dde1e5 0%,#eef0f2 40%,#eef0f2 65%,#e2e4e7 100%)}
.quote .section-title{position:absolute;top:86px;left:0;width:1200px}
.quote .section-lead{position:absolute;top:130px;left:0;width:1200px}
.field{background:var(--white);border:1px solid var(--line);font-size:12.5px;color:#333;padding:12px 18px}
.quote .btn{left:537px;top:437px;width:124px;height:46px;line-height:46px;padding:0;border-radius:23px;background:var(--black);color:var(--white)}

/* footer */
.site-footer{left:0;top:4298px;width:1200px;height:404px;background:var(--black);color:var(--white)}
.footer-brand{left:0;top:52px;width:1200px;text-align:center;font-family:var(--head);font-weight:600;font-size:30px;letter-spacing:.5px;display:flex;justify-content:center;align-items:center;gap:14px}
.footer-brand .brand-mark{width:30px;height:30px}
.contact-item{top:148px;width:260px;text-align:center;font-size:12.5px;line-height:21px}
.contact-icon{width:40px;height:40px;border-radius:50%;background:#3a3a3a;margin:0 auto 10px;display:flex;align-items:center;justify-content:center}
.contact-item .strong{font-size:14px}
.social{top:312px;left:0;width:1200px;display:flex;justify-content:center;gap:27px}
.social span{width:20px;height:20px;border-radius:50%;background:var(--white)}
.copyright{top:360px;left:0;width:1200px;text-align:center;font-size:11.5px}
</style>
</head>
<body>

<header class="site-header abs">
  <div class="brand abs"><span class="brand-mark"></span>Harlow Ridge<br>Financial Partners</div>
  <nav class="nav abs">
    <a class="active" href="#" style="left:475px">HOME</a>
    <a href="#" style="left:561px">INVESTORS</a>
    <a href="#" style="left:673px">PROJECTS</a>
    <a href="#" style="left:776px">PARTNERS</a>
    <a href="#" style="left:880px">ABOUT</a>
    <a href="#" style="left:960px">CONTACT</a>
  </nav>
</header>

<section class="hero abs" role="img" aria-label="Businessman reviewing financial charts and market data on a dark blue screen">
  <h1 class="hero-title abs">HARLOW RIDGE FINANCIAL<br>PARTNERS</h1>
  <div class="hero-btn abs">GET STARTED</div>
  <svg class="hero-arrow abs" style="left:40px" width="22" height="40" viewBox="0 0 22 40"><path d="M19 2 L3 20 L19 38" fill="none" stroke="#fff" stroke-width="2"/></svg>
  <svg class="hero-arrow abs" style="left:1138px" width="22" height="40" viewBox="0 0 22 40"><path d="M3 2 L19 20 L3 38" fill="none" stroke="#fff" stroke-width="2"/></svg>
</section>

<section class="about abs">
  <svg class="abs" style="left:170px;top:62px" width="390" height="452" viewBox="0 0 390 452">
    <defs>
      <linearGradient id="aboutPhoto" x1="0" y1="0" x2="1" y2="1">
        <stop offset="0" stop-color="#3b5d78"/>
        <stop offset=".5" stop-color="#8a9aa6"/>
        <stop offset="1" stop-color="#d8d4cc"/>
      </linearGradient>
    </defs>
    <polygon points="200,14 390,124 390,340 200,450 10,340 10,124" fill="#4a4a4a"/>
    <polygon points="190,0 380,110 380,326 190,436 0,326 0,110" fill="url(#aboutPhoto)" role="img" aria-label="Advisor in glasses writing notes beside a laptop"/>
  </svg>
  <h2 class="about-title abs">ABOUT HARLOW RIDGE<br>FINANCIAL PARTNERS</h2>
  <p class="about-text abs">Sed ut perspiciatis unde omnis iste natus error sit voluptatem accusantium doloremque laudantium, totam rem aperiam, eaque ipsa quae ab illo inventore veritatis et quasi architecto beatae vitae dicta sunt explicabo. Nemo enim ipsam voluptatem quia voluptas sit aspernatur aut odit aut fugit, sed quia consequuntur magni dolores eos qui ratione voluptatem sequi nesciunt. Neque porro quisquam est, qui dolorem ipsum quia dolor sit amet, consectetur, adipisci velit, sed quia.</p>
  <span class="btn btn-dark abs">READ MORE</span>
</section>

<section class="projects abs">
  <h2 class="section-title">OUR PROJECTS</h2>
  <p class="section-lead">Sed ut perspiciatis unde omnis iste natus error sit voluptatem accusantium<br>doloremque laudantium, totam rem aperiam, eaque isaaeab</p>

  <article class="card abs" style="left:172px;top:202px"><div class="card-img" role="img" aria-label="Hands reviewing printed financial charts" style="background:linear-gradient(135deg,#5a4c44,#bfc4c9 60%,#e9ecef)"></div><h3 class="card-title">Lorem ipsum dolorsit ametcons loreecte</h3></article>
  <article class="card abs" style="left:467px;top:202px"><div class="card-img" role="img" aria-label="Analyst pointing a pen at a bar chart report" style="background:linear-gradient(135deg,#e6e8ea,#8fa3b8 55%,#34506e)"></div><h3 class="card-title">Lorem ipsum dolorsit ametcons loreecte</h3></article>
  <article class="card abs" style="left:760px;top:202px"><div class="card-img" role="img" aria-label="Digital stock market graph in blue tones" style="background:linear-gradient(135deg,#dbe4ea,#5f8db0 50%,#1d3c57)"></div><h3 class="card-title">Lorem ipsum dolorsit ametcons loreecte</h3></article>
  <article class="card abs" style="left:172px;top:494px"><div class="card-img" role="img" aria-label="Coin stacks growing with a plant and a retirement figure" style="background:linear-gradient(135deg,#f0e2c2,#9a8a5a 50%,#4f6b3a)"></div><h3 class="card-title">Lorem ipsum dolorsit ametcons loreecte</h3></article>
  <article class="card abs" style="left:467px;top:494px"><div class="card-img" role="img" aria-label="Man working on a laptop at a desk" style="background:linear-gradient(135deg,#2b2f33,#6b6f72 50%,#c9a87c)"></div><h3 class="card-title">Lorem ipsum dolorsit ametcons loreecte</h3></article>
  <article class="card abs" style="left:760px;top:494px"><div class="card-img" role="img" aria-label="Team meeting around a tablet in an office" style="background:linear-gradient(135deg,#c4a07a,#8a7060 45%,#d0812f)"></div><h3 class="card-title">Lorem ipsum dolorsit ametcons loreecte</h3></article>
</section>

<div class="band-strip abs"></div>
<section class="band abs" role="img" aria-label="Dark background with faint financial interface graphics">
  <h2 class="band-title abs">SED UT PERSPICIATIS UNDE OMNIS ISTE NATUS<br>ERROR SIT VOLUPTATEM ACCUSANTIUM</h2>
  <div class="band-btn abs">INVESTORS INFO</div>
</section>

<section class="inprocess abs">
  <h2 class="inprocess-title abs">PROJECTS IN-PROCESS</h2>
  <p class="inprocess-text abs">Lorem ipsum dolor sit amet, consectetur adipiscing elit, sed do eiusmod tempor incididunt ut labore et dolore magna aliqua. Ut enim ad minim veniam, quis nostrud exercitation ullamco laboris nisi ut aliquip ex ea commodo consequat. Duis aute irure dolor in reprehenderit in voluptateorem ipsum dolor sit amet, consectetur adipiscing elit, sed do eiusmod tempor incididunt ut labore et dolore magna aliqua. Ut enim ad minim veniam, quis nostrud exercitation ullamco laboris nisi ut aliquip ex ea commodo conse uis aute irure dolor in reprehende</p>
  <span class="btn btn-dark abs">READ MORE</span>
  <div class="inprocess-img abs" role="img" aria-label="Business professional at a laptop in a bright office"></div>
</section>

<section class="partners abs">
  <h2 class="section-title">PARTNER BIOS</h2>
  <p class="section-lead">Sed ut perspiciatis unde omnis iste natus error sit voluptatem accusantium<br>doloremque laudantium, totam rem aperiam, eaque isaaeab</p>

  <div class="bio abs" style="left:139px"><div class="bio-photo" role="img" aria-label="Portrait of partner Aldo Brenner"></div><h3 class="bio-name">ALDO BRENNER</h3><div class="bio-rule"></div><p class="bio-text">Sed ut perspiciatis undemnien<br>atus error sit volutatespiciatisdem<br>nissten atus error sit voluam</p><div class="bio-link"></div></div>
  <div class="bio-divider abs" style="left:444px"></div>
  <div class="bio abs" style="left:449px"><div class="bio-photo" role="img" aria-label="Portrait of partner Tomas Velde"></div><h3 class="bio-name">TOMAS VELDE</h3><div class="bio-rule"></div><p class="bio-text">Sed ut perspiciatis undemnien<br>atus error sit volutatespiciatisdem<br>nissten atus error sit voluam</p><div class="bio-link"></div></div>
  <div class="bio-divider abs" style="left:753px"></div>
  <div class="bio abs" style="left:758px"><div class="bio-photo" role="img" aria-label="Portrait of partner Marcus Hale"></div><h3 class="bio-name">MARCUS HALE</h3><div class="bio-rule"></div><p class="bio-text">Sed ut perspiciatis undemnien<br>atus error sit volutatespiciatisdem<br>nissten atus error sit voluam</p><div class="bio-link"></div></div>
</section>

<section class="quote abs" role="img" aria-label="Faded city office towers in the background">
  <h2 class="section-title">GET A REQUEST QUOTE</h2>
  <p class="section-lead">Sed ut perspiciatis unde omnis iste natus error sit voluptatem<br>accusantium doloremque laudantium, totam rem aper</p>
  <div class="field abs" style="left:331px;top:230px;width:264px;height:41px">Name:</div>
  <div class="field abs" style="left:604px;top:230px;width:264px;height:41px">Phone:</div>
  <div class="field abs" style="left:331px;top:282px;width:264px;height:41px">Email:</div>
  <div class="field abs" style="left:604px;top:282px;width:264px;height:41px">Subject:</div>
  <div class="field abs" style="left:331px;top:333px;width:537px;height:80px">Message:</div>
  <span class="btn abs">SUBMIT</span>
</section>

<footer class="site-footer abs">
  <div class="footer-brand abs"><span class="brand-mark"></span>Harlow Ridge Financial Partners</div>

  <div class="contact-item abs" style="left:258px">
    <div class="contact-icon"><svg width="14" height="18" viewBox="0 0 14 18"><path d="M7 0C3.1 0 0 3 0 6.8 0 11.5 7 18 7 18s7-6.5 7-11.2C14 3 10.9 0 7 0zm0 9.3A2.5 2.5 0 1 1 7 4.3a2.5 2.5 0 0 1 0 5z" fill="#fff"/></svg></div>
    PO Box 4820<br>Calder Ave Suite 220
  </div>
  <div class="contact-item abs" style="left:469px">
    <div class="contact-icon"><svg width="16" height="16" viewBox="0 0 16 16"><path d="M3.3 0.5l2.4 3.2-1.5 1.9c.9 2 2.4 3.5 4.3 4.4l1.9-1.5 3.2 2.4-1.2 3c-.2.5-.7.8-1.3.7C5.4 14 2 10.6 1.3 4.9c0-.6.2-1.1.8-1.3z" fill="#fff"/></svg></div>
    Phone:<br><span class="strong">+1 555 013 4477</span>
  </div>
  <div class="contact-item abs" style="left:683px">
    <div class="contact-icon"><svg width="17" height="13" viewBox="0 0 17 13"><rect x="0" y="0" width="17" height="13" rx="1.5" fill="#fff"/><path d="M1 1.5l7.5 6 7.5-6" fill="none" stroke="#3a3a3a" stroke-width="1.4"/></svg></div>
    Email:<br>info@harlowridgefp.com
  </div>

  <div class="social abs"><span></span><span></span><span></span><span></span></div>
  <p class="copyright abs">© 2020 Harlow Ridge Financial Partners.. All rights reserved.</p>
</footer>

</body>
</html>
```